CONTEMPORARY Canva Art Design for Christians

I need a canvas art design on Christianity. The design must be in 3 SIMPLE dimensions: 12x 18 inches / 28 x 24 inches / 30 x 40 inches
The design must be accompanied by christian quote.
The christian quote can be "As For Me And My House We Will Serve The Lord (Joshua 24:15)" or any other quote that is good for display in a christian home.

I DON'T WANT THE TRADITIONAL CHRISTIAN DESIGN.. I WANT COLOURFUL, MEANINGFUL and CONTEMPORARY, MODERN DESIGN. And stay away from the scary image of Jesus in dark background, it only makes the home more scary not holy!

Target Market(s)

Christians

Colors

Designer to choose colors to be used in the design.

Requirements
Must have
• A graphic design and a christian quote that is powerful and edifies the soul. Great for display at home. Great use of colours to enhance the message.
Nice to have
• I wish to see great unique design with strong use of colours, images to enhance the scripture. It must glorify Jesus.
Should not have
• Should not be dull.

```html
<!DOCTYPE html>
<html lang="en">
<head>
<meta charset="UTF-8">
<title>As For Me And My House – Canvas Art</title>
<link rel="stylesheet" href="https://fonts.googleapis.com/css2?family=Tinos&family=Roboto+Condensed:wght@300&display=swap">
<style>
  :root {
    --page-bg: #2b2d31;
    --sky-deep: #0a2fb4;
    --sky-mid: #2f6fd8;
    --sky-light: #9cc8f2;
    --glow: #ffffff;
    --ink: #050505;
  }
  html, body {
    margin: 0;
    padding: 0;
    width: 1200px;
    height: 1200px;
    overflow: hidden;
    background: var(--page-bg);
  }
  .canvas-art {
    position: absolute;
    left: 0;
    top: 200px;
    width: 1200px;
    height: 800px;
    overflow: hidden;
    background:
      radial-gradient(ellipse 620px 480px at 600px 190px, var(--glow) 0%, rgba(255,255,255,0.85) 25%, rgba(255,255,255,0) 70%),
      linear-gradient(180deg, var(--sky-light) 0%, var(--sky-mid) 55%, var(--sky-deep) 100%);
  }
  .heavenly-sky {
    position: absolute;
    inset: 0;
  }
  .light-cross {
    position: absolute;
    inset: 0;
  }
  .verse {
    position: absolute;
    margin: 0;
    color: var(--ink);
    font-family: "Tinos", "Times New Roman", serif;
    font-weight: 400;
    line-height: 1;
    white-space: nowrap;
  }
  .verse-line-one {
    left: 128px;
    top: 472px;
    font-size: 71px;
    letter-spacing: -1px;
  }
  .verse-line-two {
    left: 128px;
    top: 551px;
    font-size: 59px;
    letter-spacing: -1px;
  }
  .verse-emphasis {
    left: 712px;
    top: 522px;
    font-size: 166px;
    letter-spacing: -2px;
  }
  .verse-reference {
    position: absolute;
    right: 169px;
    top: 702px;
    margin: 0;
    color: var(--ink);
    font-family: "Roboto Condensed", "Arial Narrow", sans-serif;
    font-weight: 300;
    font-size: 31px;
    line-height: 1;
    white-space: nowrap;
  }
</style>
</head>
<body>
  <main class="canvas-art">
    <div class="heavenly-sky" role="img" aria-label="Bright blue sky with clouds and rays of light, a white dove descending with open wings"></div>
    <svg class="light-cross" width="1200" height="800" viewBox="0 0 1200 800" aria-hidden="true">
      <path d="M586 62 H634 V152 H751 V208 H634 V330 H586 V208 H470 V152 H586 Z" fill="#ffffff" opacity="0.75"/>
    </svg>
    <p class="verse verse-line-one">AS FOR ME AND MY HOUSE</p>
    <p class="verse verse-line-two">WE WILL SERVE THE</p>
    <p class="verse verse-emphasis">Lord</p>
    <p class="verse-reference">(JOSHUA 24:15)</p>
  </main>
</body>
</html>
```